Looking for someone to design a business card for my plumbing business Quandor Plumbing Solutions I want the background also to be black, must attract clients. If possible I want the front to be the logo and the back to show maybe the details.

Target Market(s)

Clients

Industry/Entity Type

Plumbing maintenance

Contact Information for Business Card

Name: Felix, Contact: 0461 539 207, Email: quandorplumbingsolutions@mailbrook.example, Licence number 728093K

Font styles to use
Other font styles liked:
• as per logo maybe?

Colors

Designer to choose colors to be used in the design.

Requirements
Nice to have
• stating the service I provide, emergency plumbing, plumbing maintenance, drainage maintenance, block sewer and stormwater, camera and locating.

```html
<!DOCTYPE html>
<html lang="en">
<head>
<meta charset="utf-8">
<title>Quandor Plumbing Solutions – Business Card</title>
<link href="https://fonts.googleapis.com/css2?family=Montserrat:wght@400;700&display=swap" rel="stylesheet">
<style>
  :root {
    --page-bg: #151515;
    --card-bg: #1f1f1f;
    --blue: #4a8fd0;
    --white: #f2f2f2;
    --text: #e6e6e6;
    --faint: #2c2c2c;
  }
  * { margin: 0; padding: 0; box-sizing: border-box; }
  html, body { width: 1200px; height: 1059px; overflow: hidden; }
  body {
    background: var(--page-bg);
    font-family: "Montserrat", sans-serif;
    position: relative;
  }
  .card {
    position: absolute;
    width: 690px;
    height: 392px;
    background: var(--card-bg);
    border-radius: 18px;
    box-shadow: 0 10px 24px rgba(0,0,0,.5);
    overflow: hidden;
  }
  .card--front { left: 256px; top: 89px; }
  .card--back { left: 255px; top: 548px; }

  .brand {
    position: absolute;
    right: 44px;
    top: 60px;
    display: flex;
    align-items: center;
    gap: 12px;
  }
  .brand__mark {
    width: 30px; height: 30px;
    border-radius: 50%;
    background: var(--blue);
  }
  .brand__name {
    color: var(--white);
    font-weight: 700;
    font-size: 26px;
    line-height: 1.15;
    text-transform: uppercase;
    text-align: right;
  }

  .person { position: absolute; left: 39px; top: 196px; }
  .person__name {
    color: var(--blue);
    font-weight: 700;
    font-size: 29px;
    line-height: 1;
    text-transform: uppercase;
  }
  .person__role { color: var(--text); font-size: 15px; margin-top: 2px; }

  .divider {
    position: absolute;
    left: 39px; top: 257px;
    width: 607px; height: 1.5px;
    background: var(--blue);
  }
  .licence {
    position: absolute;
    left: 424px; top: 257px;
    width: 222px; height: 25px;
    background: var(--blue);
    clip-path: polygon(0 0, 100% 0, 100% 100%, 16px 100%);
    color: var(--white);
    font-size: 14.5px;
    line-height: 25px;
    text-align: right;
    padding-right: 9px;
  }

  .contacts {
    position: absolute;
    left: 39px; top: 277px;
    list-style: none;
  }
  .contacts__item {
    display: flex;
    align-items: center;
    gap: 7px;
    height: 26px;
    color: var(--text);
    font-size: 15.5px;
  }
  .contacts__icon { width: 13px; height: 13px; flex: none; }

  .back-brand {
    position: absolute;
    left: 0; right: 0; top: 110px;
    text-align: center;
    color: var(--faint);
    font-weight: 700;
    font-size: 44px;
    line-height: 1.1;
    text-transform: uppercase;
  }
  .services {
    position: absolute;
    left: 0; right: 0; top: 312px;
    text-align: center;
    color: var(--text);
    font-size: 15.5px;
    line-height: 27px;
  }
  .services__dot { color: var(--blue); padding: 0 6px; }
</style>
</head>
<body>

<section class="card card--front">
  <div class="brand">
    <span class="brand__mark"></span>
    <div class="brand__name">Quandor<br>Plumbing Solutions</div>
  </div>

  <div class="person">
    <div class="person__name">Felix</div>
    <div class="person__role">Founder &amp; CEO</div>
  </div>

  <div class="divider"></div>
  <div class="licence">Licence number 728093K</div>

  <ul class="contacts">
    <li class="contacts__item">
      <svg class="contacts__icon" viewBox="0 0 24 24"><path fill="#4a8fd0" d="M6.6 10.8a15.1 15.1 0 0 0 6.6 6.6l2.2-2.2c.3-.3.7-.4 1-.2 1.1.4 2.3.6 3.6.6.6 0 1 .4 1 1V20c0 .6-.4 1-1 1A17 17 0 0 1 3 4c0-.6.4-1 1-1h3.5c.6 0 1 .4 1 1 0 1.3.2 2.5.6 3.6.1.3 0 .7-.2 1z"/></svg>
      0461 539 207
    </li>
    <li class="contacts__item">
      <svg class="contacts__icon" viewBox="0 0 24 24"><path fill="#4a8fd0" d="M2 5h20v14H2z"/><path fill="none" stroke="#1f1f1f" stroke-width="1.8" d="M2 5l10 8 10-8"/></svg>
      quandorplumbingsolutions@mailbrook.example
    </li>
    <li class="contacts__item">
      <svg class="contacts__icon" viewBox="0 0 24 24"><circle cx="12" cy="12" r="11" fill="#4a8fd0"/></svg>
      @QuandorPlumbingSolutions
    </li>
  </ul>
</section>

<section class="card card--back">
  <div class="back-brand">Quandor<br>Plumbing Solutions</div>
  <p class="services">
    Emergency plumbing<span class="services__dot">•</span>Plumbing maintenance<span class="services__dot">•</span>Drainage maintenance<br>
    Block sewer and stormwater<span class="services__dot">•</span>Camera and locating
  </p>
</section>

</body>
</html>
```